Redesign 2016 Digital Marketing Website and Convert to Wordpress

Technology needed to integrate:

- redesign and convert to wordpress
- gravity forms
- malware and hacker defense / honeypot (must be very secure from hackers)
- I want gravity forms to be a flow that asks many questions with icons and progress bar.
- 1 home page design
- 1 blog design
- 1 design for internal page content
- 1 multi step gravity form
I want to focus on SMB's. We are a marketing agency thats been around since 2016.

Site is: tallpine.agency

I am looking to redesign the homepage, blog page and services page. The services page will be a template for all inner pages of the site. All content needs to be moved into the new design.

I want to get ride of the weird video.

I need you to install gravity forms pro model so we can pass utms.

I need the gravity form to be a multi step form with icons.

All "contact us" or "get a free assesments" call to actions will go to this form only.

step 1:
what is your website

step 2:
what industry are you in
- option
- Home Services
- Legal
- Ecommerce
- Lead Gen

No matter which one they select its going to produce a differnt calculator for them.

Law:
How many leads did you get last month
how much is each ase worth on average
How much revenue do you want to make

Home servicse:
How many bookings did you get last month
How much is each service worht on average
How much revenue do you wangt to make

Ecommerce:
What is your average order value
How muny purchases did you have last month
How much revenue did you drive
How much revenue do you want to drive

For lead gen:
How many leads did you get lawt month
How much revenue did they generate

Step 3:
What is your current advertising budget

step 4:
Do you have a CRM and if so what is it

Step 5:
What is your personal informagtion
name
email
phone

Let me know if this is enough to get you going

Small and medium sized law firms, ecommerce, home services and lead gen customers.

We are a digital marketing agency

• Use whats on the current site and improve upon it

• Must be very secure, developed into a wordpress website. using gravity forms. remove my photo and my staffs photo, depersonalize it so it doesnt mention me or sam crolley. Use the same color scheme. I am looking to redesign the homepage, blog page and services page. The services page will be a template for all inner pages of the site. All content needs to be moved into the new design. I want to get ride of the weird video. I need you to install gravity forms pro model so we can pass utms. I need the gravity form to be a multi step form with icons. All "contact us" or "get a free assesments" call to actions will go to this form only. step 1: what is your website step 2: what industry are you in - option - Home Services - Legal - Ecommerce - Lead Gen No matter which one they select its going to produce a differnt calculator for them. Law: How many leads did you get last month how much is each ase worth on average How much revenue do you want to make Home servicse: How many bookings did you get last month How much is each service worht on average How much revenue do you wangt to make Ecommerce: What is your average order value How muny purchases did you have last month How much revenue did you drive How much revenue do you want to drive For lead gen: How many leads did you get lawt month How much revenue did they generate How much revenue do you want to make Step 3: What is your current advertising budget step 4: Do you have a CRM and if so what is it Step 5: What is your personal informagtion name email phone Let me know if this is enough to get you going
• SHOULD NOT BE SLOPPY, I AM LOOKING FOR ATTENTION TO DETAIL.

```html
<!DOCTYPE html>
<html lang="en">
<head>
<meta charset="utf-8">
<title>Tall Pine Growth Marketing – Get a Free Assessment</title>
<link href="https://fonts.googleapis.com/css2?family=Poppins:wght@400;500;600;700;800&display=swap" rel="stylesheet">
<style>
  :root{
    --brand:#6e1414;
    --brand-deep:#5a0f10;
    --ink:#333333;
    --ink-soft:#4a4a4a;
    --muted:#7a7a7a;
    --nav:#2b2b2b;
    --line:#cfcfcf;
    --field-border:#bdbdbd;
    --white:#ffffff;
  }
  *{box-sizing:border-box;margin:0;padding:0}
  html,body{width:716px;height:1200px;overflow:hidden;background:var(--white)}
  body{position:relative;font-family:"Poppins",sans-serif;color:var(--ink)}
  .abs{position:absolute}

  /* Header */
  .brand-mark{position:absolute;border-radius:50%;border:2.5px solid var(--brand)}
  .brand-name{position:absolute;font-weight:400;color:var(--muted);letter-spacing:1.5px;white-space:nowrap;line-height:1}
  .brand-tag{position:absolute;font-size:5.5px;letter-spacing:3px;color:var(--muted);white-space:nowrap;line-height:1}
  .call-now{left:326px;top:20px;font-size:10.6px;font-weight:600;color:var(--ink-soft);white-space:nowrap;line-height:14px}
  .call-now b{color:var(--brand);font-weight:700}
  .header-cta{left:525px;top:12.5px;width:147px;height:28.5px;background:var(--brand);color:var(--white);font-size:9.6px;font-weight:600;display:flex;align-items:center;justify-content:center;letter-spacing:.2px}

  .main-nav{left:0;top:54px;width:716px;height:32px;background:var(--nav)}
  .main-nav span{position:absolute;top:0;line-height:32px;font-size:8.2px;color:var(--white);letter-spacing:.3px}

  /* Assessment form */
  .page-title{left:45px;top:118px;font-size:22px;font-weight:800;color:var(--ink);letter-spacing:.3px;line-height:28px;white-space:nowrap}
  .title-rule{left:45px;top:153px;width:56px;height:2px;background:var(--brand)}
  .timeline{left:49.5px;top:220px;width:1px;height:305px;background:var(--field-border)}
  .step-dot{position:absolute;width:10.6px;height:10.6px;border-radius:50%;background:#777;left:44.7px}
  .step-dot.active{background:var(--brand);box-shadow:0 0 0 2.5px #e6e6e6}
  .step-label{position:absolute;left:65px;font-size:10px;font-weight:700;color:#6a6a6a;line-height:12px;white-space:nowrap}
  .step-label.active{color:var(--brand)}
  .field-label{position:absolute;left:111px;font-size:10px;font-weight:500;color:var(--ink);line-height:12px;white-space:nowrap}
  .field{position:absolute;height:30px;border:1px solid var(--field-border);background:var(--white);font-size:7.5px;color:var(--ink);padding-left:8px;display:flex;align-items:center}
  .field.select{justify-content:space-between;padding-right:8px}
  .submit-btn{left:111px;top:533px;width:142px;height:30px;background:var(--brand);color:var(--white);font-size:12px;font-weight:700;display:flex;align-items:center;justify-content:center}

  /* CTA band */
  .cta-band{left:0;top:619px;width:716px;height:204px;background:linear-gradient(100deg,#5e1012 0%,#6b1416 45%,#7a1a1c 70%,#5c0f11 100%)}
  .cta-title{left:45px;top:685px;font-size:21px;font-weight:800;color:var(--white);line-height:28px;white-space:nowrap;letter-spacing:.2px}
  .cta-sub{left:44px;top:719px;font-size:12.5px;color:var(--white);line-height:16px;white-space:nowrap}
  .cta-rule{left:45px;top:750px;width:56px;height:2px;background:var(--white)}
  .cta-btn{position:absolute;left:511px;width:162px;border:1.2px solid var(--white);color:var(--white);font-size:8.7px;font-weight:600;display:flex;align-items:center;justify-content:center}
  .cta-or{left:581.5px;top:709.5px;width:20px;height:20px;border-radius:50%;border:1.2px solid var(--white);background:var(--brand-deep);color:var(--white);font-size:7.5px;font-weight:600;display:flex;align-items:center;justify-content:center}

  /* Footer */
  .partner-badge{left:247px;top:844px;width:123px;height:52px;border-radius:2px;background:#ececec}
  .partner-badge::before{content:"";position:absolute;left:0;top:0;width:14px;height:52px;background:#e04a3a}
  .listing-badge{left:409.5px;top:843.5px;width:53px;height:53px;border-radius:50%;background:#1d3f5e;border:2px solid #d7dde4}
  .follow-title{left:528px;top:847px;font-size:10.6px;font-weight:500;color:var(--ink-soft);letter-spacing:.4px;line-height:14px}
  .social{position:absolute;top:871px;width:19px;height:19px;border-radius:50%;background:var(--ink-soft)}
  .footer-divider{left:0;width:716px;height:1px;background:#e2e2e2}
  .footer-col{position:absolute;top:940px}
  .footer-col h3{font-size:14.5px;font-weight:700;color:var(--ink-soft);line-height:18px;letter-spacing:.2px;margin-bottom:5px;white-space:nowrap}
  .footer-col ul{list-style:none}
  .footer-col li{font-size:8px;color:var(--ink-soft);line-height:10px;margin-bottom:9.5px;white-space:nowrap;letter-spacing:.2px}
  .footer-col.guides li{line-height:13px;margin-bottom:6.5px}
  .copyright{left:0;width:716px;top:1170px;text-align:center;font-size:8px;color:var(--ink-soft);line-height:12px}
</style>
</head>
<body>

<!-- Header -->
<header>
  <div class="brand-mark" style="left:45px;top:8.5px;width:36px;height:36px"></div>
  <div class="brand-name" style="left:91px;top:15px;font-size:15px">TALL PINE</div>
  <div class="brand-tag" style="left:92px;top:33.5px">GROWTH MARKETING</div>
  <div class="abs call-now">OR CALL US NOW : <b>(480) 555-0142</b></div>
  <div class="abs header-cta">GET A FREE CONSULTATION</div>
</header>

<nav class="abs main-nav">
  <span style="left:105px">HOME</span>
  <span style="left:157px">ABOUT</span>
  <span style="left:214px">INDUSTRIES</span>
  <span style="left:290px">SERVICES</span>
  <span style="left:358px">RESOURCES</span>
  <span style="left:437px">TRAINING</span>
  <span style="left:505px">BLOG</span>
  <span style="left:555px">CONTACT US</span>
</nav>

<!-- Assessment form -->
<main>
  <h1 class="abs page-title">GET A FREE ASSESSMENTS</h1>
  <div class="abs title-rule"></div>

  <div class="abs timeline"></div>

  <div class="step-dot active" style="top:214.7px"></div>
  <div class="step-label active" style="top:214px">STEP 1</div>
  <div class="field-label" style="top:185px">What is your website</div>
  <div class="field" style="left:111px;top:204.5px;width:295px">Enter business name</div>

  <div class="step-dot" style="top:278.7px"></div>
  <div class="step-label" style="top:278px">STEP 2</div>
  <div class="field-label" style="top:249px">What industry are you in</div>
  <div class="field select" style="left:111px;top:268.5px;width:295px">
    <span>Select Option</span>
    <svg width="5" height="7" viewBox="0 0 5 7" aria-hidden="true"><path d="M2.5 0L5 2.8H0z M2.5 7L0 4.2H5z" fill="#222"/></svg>
  </div>

  <div class="step-dot" style="top:343.7px"></div>
  <div class="step-label" style="top:343px">STEP 3</div>
  <div class="field-label" style="top:313px">What is your current advertising budget</div>
  <div class="field" style="left:111px;top:333px;width:295px">Enter budget</div>

  <div class="step-dot" style="top:405.7px"></div>
  <div class="step-label" style="top:405px">STEP 4</div>
  <div class="field-label" style="top:376px">Do you have a CRM and if so what is it</div>
  <div class="field" style="left:111px;top:395.5px;width:295px">Enter CRM details</div>

  <div class="step-dot" style="top:469.7px"></div>
  <div class="step-label" style="top:469px">STEP 5</div>
  <div class="field-label" style="top:439px">What is your personal information</div>
  <div class="field" style="left:111px;top:459px;width:142.5px">Name</div>
  <div class="field" style="left:263px;top:459px;width:142.5px">Phone</div>
  <div class="field" style="left:111px;top:495.5px;width:294.5px">Email Address</div>

  <div class="abs submit-btn">Submit</div>
</main>

<!-- Call to action band -->
<section>
  <div class="abs cta-band" role="img" aria-label="Background photo of hands working at a laptop showing marketing charts, tinted dark red"></div>
  <h2 class="abs cta-title">CAN WE HELP YOUR BUSINESS GROW?</h2>
  <p class="abs cta-sub">Let’s have a friendly chat to find out.</p>
  <div class="abs cta-rule"></div>
  <div class="cta-btn" style="top:666px;height:33.5px">Get a Free Consultation</div>
  <div class="abs cta-or">Or</div>
  <div class="cta-btn" style="top:742px;height:34px">Give us a call: (480) 555-0142</div>
</section>

<!-- Footer -->
<footer>
  <div class="brand-mark" style="left:45px;top:852px;width:36px;height:36px"></div>
  <div class="brand-name" style="left:90px;top:859px;font-size:15px">TALL PINE</div>
  <div class="brand-tag" style="left:91px;top:877.5px">GROWTH MARKETING</div>

  <div class="abs partner-badge" role="img" aria-label="Premier partner badge"></div>
  <div class="abs listing-badge" role="img" aria-label="Client review listing badge"></div>

  <div class="abs follow-title">FOLLOW US</div>
  <div class="social" style="left:525px" role="img" aria-label="Social profile"></div>
  <div class="social" style="left:554px" role="img" aria-label="Social profile"></div>
  <div class="social" style="left:584px" role="img" aria-label="Social profile"></div>
  <div class="social" style="left:618px" role="img" aria-label="Social profile"></div>
  <div class="social" style="left:652px" role="img" aria-label="Social profile"></div>

  <div class="abs footer-divider" style="top:915.5px"></div>

  <div class="footer-col" style="left:45px">
    <h3>QUICK LINKS</h3>
    <ul><li>About</li><li>Industries</li><li>Services</li><li>Resources</li><li>Training</li><li>Blog</li><li>Contact Us</li></ul>
  </div>
  <div class="footer-col" style="left:190px">
    <h3>SERVICES</h3>
    <ul><li>Programmatic Advertising</li><li>Search Engine Marketing (SEM)</li><li>Search Engine Optimization (SEO)</li><li>Content Marketing</li><li>Email Marketing</li><li>Paid Search Advertising</li><li>Paid Social Advertising</li></ul>
  </div>
  <div class="footer-col" style="left:367px">
    <h3>INDUSTRIES</h3>
    <ul><li>Ecommerce</li><li>Electricians</li><li>Financial Services Marketing</li><li>Home Builders</li><li>Home Services</li><li>Hvac Companies</li><li>Cosmetic Surgery Centers</li><li>Dental Marketing</li></ul>
  </div>
  <div class="footer-col guides" style="left:527px">
    <h3>GUIDES</h3>
    <ul>
      <li>Ultimate Guide On Growing Your<br>Medical Practice Business</li>
      <li>Legal Marketing Strategy Guide For<br>Law Firm Offices</li>
      <li>Ultimate Social Ads Guide To<br>Skyrocket Your Leads And Sales</li>
      <li>Ultimate Guide To Search<br>Engine Queries</li>
    </ul>
  </div>

  <div class="abs footer-divider" style="top:1151.5px"></div>
  <p class="abs copyright">Copyright © 2024 CompanyName&nbsp; All Rights Reserved. Privacy Policy, Terms Of Use, Press &amp; Media, Cookie Policy</p>
</footer>

</body>
</html>
```